Vantrel System Web Page Design

This project is to design 6 pages of a web based medical system for clinics, hospitals, drugs suppliers, general items suppliers, insurance company, laboratories and patients (basically all parties which could be involved in).We want the designs of the browser, button, icon and layout are based on Zeltor, which is user friendly, looks professional, simple and neat but with powerful functions. We have uploaded few pictures of another system, please do not copy its design because this is not what we are looking for, the pictures are for you to know the elements should be included in our pages. Vantrel web-base system, design 6 pages1. Login PageShould include the following elements-company id with input field-login id with input field-password with input field2. Main Page (Navigation page)Should include the following elements-Appointment-Consultation-Patient-Drugs inventory -General supplies inventory -Laboratory-Suppliers-Insurance-Reports 3. Appointment PageShould include all the the elements in the respective pictures plus the followings-Daily View, Weekly View, Monthly View buttons4. Consultation PageShould include all the the elements in the respective picture5. Patient Page5.1 General information Should include all the the elements in the respective picture5.2 medical history/lab reportsShould include all the the elements in the respective picture plus the followings-Notify patient button-Share report button.
Updated on 28 Nov:
Please stop using Harbor Suite in your designs which is not the name of our system. We have just rename our system to Vantrel, please take note.
We need the system to look professional not playful, do not use too many colors and playful icons.

```html
<!DOCTYPE html>
<html lang="en">
<head>
<meta charset="utf-8">
<title>Vantrel — Home</title>
<link href="https://fonts.googleapis.com/css2?family=Lato:wght@400;700;900&family=Nunito+Sans:wght@400;700;800&family=Raleway:wght@300&display=swap" rel="stylesheet">
<style>
  :root{
    --teal:#1bbcd0;
    --teal-soft:#5fd0dd;
    --navy:#2d3a7a;
    --icon:#14476b;
    --ink:#0d0d0d;
    --footer-bg:#ebe8e8;
    --footer-ink:#a9a9a9;
    --white:#ffffff;
  }
  *{box-sizing:border-box;margin:0;padding:0}
  html,body{width:920px;height:1200px;overflow:hidden;background:var(--white)}
  body{position:relative;font-family:"Nunito Sans",Arial,sans-serif}

  .hero{position:absolute;left:0;top:0;width:920px;height:588px;overflow:hidden}
  .hero-photo{position:absolute;inset:0;
    background:
      radial-gradient(ellipse 45% 70% at 80% 40%, #d9b98a 0%, rgba(217,185,138,0.55) 40%, rgba(255,255,255,0) 75%),
      linear-gradient(100deg,#eef1f5 0%,#e4e9ef 45%,#d8dee5 70%,#cfc5b5 100%);}

  .site-header{position:absolute;left:0;top:0;width:920px;height:55px;border-bottom:1px solid #9a9a9a;
    display:flex;align-items:center;padding:0 30px 0 38px}
  .brand{font-family:"Nunito Sans",sans-serif;font-weight:800;color:var(--teal);font-size:19px;letter-spacing:1px}
  .nav{margin-left:auto;display:flex;align-items:center;gap:22px;font-size:13px;color:#1a1a1a}
  .nav-lang{display:flex;align-items:center;gap:6px}
  .nav-phone{background:var(--teal);color:var(--white);border-radius:5px;padding:8px 8px;font-size:13px}

  .hero-title{position:absolute;left:34px;top:168px;font-family:"Lato",sans-serif;font-weight:900;
    font-size:47px;line-height:67px;letter-spacing:4.8px;color:var(--ink)}
  .hero-title .accent{color:var(--teal)}

  .btn-pill{position:absolute;top:418px;height:54px;border-radius:27px;display:flex;align-items:center;
    gap:10px;font-family:"Lato",sans-serif;font-weight:700;font-size:15px;letter-spacing:-0.3px;text-decoration:none}
  .btn-book{left:34px;width:231px;background:var(--navy);color:var(--white);padding-left:14px}
  .btn-consult{left:318px;width:244px;border:1.5px solid var(--navy);color:var(--navy);padding-left:9px}

  .features-title{position:absolute;left:38px;top:630px;font-family:"Lato",sans-serif;font-weight:900;
    font-size:43px;letter-spacing:3px;color:var(--ink)}
  .features-title .accent{color:var(--teal)}
  .features-underline{position:absolute;left:38px;top:681px;width:240px;height:4px;background:var(--teal-soft)}

  .feature{position:absolute;width:157px;display:flex;flex-direction:column;align-items:center}
  .feature svg{height:80px;width:90px}
  .feature-btn{width:157px;height:42px;background:var(--teal);color:var(--white);border-radius:4px;
    display:flex;align-items:center;justify-content:center;font-weight:800;font-size:18px;margin-top:15px}

  .site-footer{position:absolute;left:0;top:1144px;width:920px;height:56px;background:var(--footer-bg);
    border-top:1px solid #c9c9c9;display:flex;align-items:center;justify-content:center;
    font-family:"Raleway",sans-serif;font-weight:300;font-size:14px;color:var(--footer-ink)}
</style>
</head>
<body>
  <section class="hero">
    <div class="hero-photo" role="img" aria-label="Photo of a dentist in safety glasses and a face mask at work in a bright clinic"></div>
    <header class="site-header">
      <div class="brand">Vantrel</div>
      <nav class="nav">
        <span class="nav-lang">Language
          <svg width="11" height="7" viewBox="0 0 11 7"><path d="M1 1l4.5 4.5L10 1" fill="none" stroke="#555" stroke-width="1"/></svg>
        </span>
        <span>About us</span>
        <span class="nav-phone">(000)5550 1234</span>
      </nav>
    </header>
    <h1 class="hero-title">We provide best<br>quality Sevrvice&nbsp; for<br>you medical <span class="accent">problem</span></h1>
    <a class="btn-pill btn-book">BOOK AN APPOINTMENT
      <svg width="24" height="20" viewBox="0 0 24 20"><path d="M12 18.5S2 12.5 2 6.5A4.8 4.8 0 0 1 12 4a4.8 4.8 0 0 1 10 2.5c0 6-10 12-10 12z" fill="none" stroke="#fff" stroke-width="1.3"/><path d="M3 10h5l2-3 3 6 2-3h6" fill="none" stroke="#fff" stroke-width="1.3"/></svg>
    </a>
    <a class="btn-pill btn-consult">CONSULT AN APPOINTMENT
      <svg width="20" height="26" viewBox="0 0 20 26"><path d="M3 2v7a5 5 0 0 0 10 0V2" fill="none" stroke="#2d3a7a" stroke-width="1.4"/><path d="M8 14v5a3 3 0 0 0 6 0v-6" fill="none" stroke="#2d3a7a" stroke-width="1.4"/><circle cx="14" cy="11" r="2" fill="none" stroke="#2d3a7a" stroke-width="1.4"/></svg>
    </a>
  </section>

  <h2 class="features-title">Enjoy more <span class="accent">features</span></h2>
  <div class="features-underline"></div>

  <div class="feature" style="left:86px;top:738px">
    <svg viewBox="0 0 90 80"><g fill="none" stroke="#14476b" stroke-width="2.4"><rect x="14" y="0" width="22" height="60" rx="11" transform="rotate(35 25 30)"/><path d="M17 27l14 10"/><path d="M24 14l-4 8"/><ellipse cx="63" cy="58" rx="20" ry="6"/><path d="M43 58v12c0 3.5 9 6 20 6s20-2.5 20-6V58"/><path d="M50 69h26"/></g></svg>
    <div class="feature-btn">Drug book</div>
  </div>
  <div class="feature" style="left:382px;top:735px">
    <svg viewBox="0 0 90 80"><g fill="none" stroke="#14476b" stroke-width="2.2"><path d="M26 2h56v66H12"/><path d="M12 68a5 5 0 0 1-5-5V38h12v25a5 5 0 0 1-5 5"/><path d="M19 38V2h7"/><rect x="40" y="8" width="30" height="5"/><rect x="32" y="20" width="14" height="12"/><path d="M52 22h22M52 30h22M32 40h42M32 48h18M32 56h18"/><rect x="56" y="46" width="16" height="12"/></g></svg>
    <div class="feature-btn">Report</div>
  </div>
  <div class="feature" style="left:678px;top:738px">
    <svg viewBox="0 0 90 80"><g fill="none" stroke="#14476b" stroke-width="3.5"><circle cx="45" cy="20" r="18"/><path d="M11 78a34 34 0 0 1 68 0"/></g></svg>
    <div class="feature-btn">Patient</div>
  </div>

  <div class="feature" style="left:86px;top:947px">
    <svg viewBox="0 0 90 80"><g fill="none" stroke="#14476b" stroke-width="3.5"><circle cx="45" cy="40" r="31"/><path d="M54 28c-2-4-6-5-9-5-5 0-9 3-9 7 0 10 19 6 19 17 0 4-4 7-10 7-4 0-8-2-10-6M45 16v50"/></g></svg>
    <div class="feature-btn">Expenses</div>
  </div>
  <div class="feature" style="left:382px;top:944px">
    <svg viewBox="0 0 90 80"><g fill="none" stroke="#14476b" stroke-width="3" stroke-linejoin="round"><path d="M10 20L45 6l35 14v40L45 76 10 60z"/><path d="M10 20l35 14 35-14M45 34v42"/><path d="M28 13l35 14v10l-6-3-5 4V25L28 13"/></g></svg>
    <div class="feature-btn">Inventry</div>
  </div>
  <div class="feature" style="left:678px;top:947px">
    <svg viewBox="0 0 90 80"><g fill="none" stroke="#14476b" stroke-width="2.4"><path d="M41 8h8l2 8 6 3 7-4 6 6-4 7 3 6 8 2v8l-8 2-3 6 4 7-6 6-7-4-6 3-2 8h-8l-2-8-6-3-7 4-6-6 4-7-3-6-8-2v-8l8-2 3-6-4-7 6-6 7 4 6-3z"/><circle cx="45" cy="40" r="9"/></g></svg>
    <div class="feature-btn">Configuration</div>
  </div>

  <footer class="site-footer">Copyright (C) 1995-2010 Corvane Medical Solution Limited</footer>
</body>
</html>
```